Hemp company needs website/online store

We are a startup hemp company and we need an online storefront designed. We are very open do design, but will include our logo to help. We make 100% hemp derived products like edibles, concentrates, vapes and THCA flower. Everything is grown locally, and all products are extracted and made in house.

• I would like to highlight that we have Cannabis products that are hemp derived and 100% legal across the US. Also that all cannabis is locally grown and products are extracted and made in house and sent out for third party lab testing.

```html
<!DOCTYPE html>
<html lang="en">
<head>
<meta charset="utf-8">
<title>Sunleaf Hemp</title>
<link href="https://fonts.googleapis.com/css2?family=Lato:wght@400;700;900&family=Montserrat:wght@600;700;800&display=swap" rel="stylesheet">
<style>
:root{
  --green-dark:#4b7a2a;
  --green-lime:#86a21d;
  --green-band:#809c1c;
  --ink:#111111;
  --text:#555555;
  --muted:#777777;
  --line:#e6e6e6;
  --panel:#f4f4f4;
  --black:#000000;
  --white:#ffffff;
}
*{box-sizing:border-box;margin:0;padding:0}
html,body{width:1200px;height:3994px;overflow:hidden}
body{position:relative;background:var(--white);font-family:'Lato',sans-serif;color:var(--text)}
.abs{position:absolute}
.head-font{font-family:'Montserrat',sans-serif}

/* top bar + header */
.topbar{left:0;top:0;width:1200px;height:42px;background:var(--green-dark)}
.topbar span{position:absolute;right:111px;top:12px;color:var(--white);font-weight:700;font-size:15px}
.brand{left:110px;top:88px;font-family:'Lato',sans-serif;font-weight:900;font-size:40px;color:var(--green-dark);display:flex;align-items:center;gap:12px}
.brand i{display:block;width:34px;height:34px;background:var(--green-lime);border-radius:50%}
.search{left:523px;top:63px;width:300px;height:40px;border:1px solid var(--line);font-size:15px;color:var(--muted);padding:11px 22px}
.search svg{position:absolute;right:14px;top:12px}
.util{top:74px;font-size:15px;color:var(--muted);display:flex;align-items:center;gap:8px}
.nav{top:129px;display:flex;font-size:15px;color:var(--muted)}
.nav a{position:absolute;white-space:nowrap;text-decoration:none;color:inherit}

/* hero */
.hero{left:0;top:178px;width:1200px;height:572px;background:linear-gradient(90deg,#eef0ec 0%,#dfe3da 45%,#9fb07a 65%,#4f7a3a 85%,#2f5a2a 100%)}
.hero-title{left:110px;top:285px;font-family:'Montserrat',sans-serif;font-weight:800;font-size:50px;line-height:70px;color:var(--ink);letter-spacing:1px}
.btn{position:absolute;display:flex;align-items:center;justify-content:center;color:var(--white);font-weight:900;font-size:17px;text-decoration:none}
.btn-lime{background:var(--green-lime)}
.btn-dark{background:var(--green-dark)}

/* section headings */
.mark{position:absolute;width:40px;height:6px;background:var(--green-lime);border-radius:3px}
.h2{position:absolute;font-family:'Montserrat',sans-serif;font-weight:800;font-size:38px;color:var(--ink);letter-spacing:1px;white-space:nowrap}

/* product cards */
.card{position:absolute;top:980px;width:235px;height:413px;border:1px solid var(--line);background:var(--white);text-align:center}
.card.active{border:3px solid var(--green-lime)}
.card .photo{position:absolute;left:12px;top:15px;width:calc(100% - 24px);height:182px}
.card h3{position:absolute;top:210px;width:100%;font-family:'Montserrat',sans-serif;font-weight:700;font-size:17px;color:var(--ink)}
.card .price{position:absolute;top:254px;width:100%;font-size:13px;color:var(--muted)}
.card .price b{color:var(--green-dark);font-family:'Montserrat',sans-serif;font-size:16px}
.card .cart{position:absolute;left:19px;top:289px;width:195px;height:40px;display:flex}
.card .cart span{flex:1;background:var(--green-dark);color:var(--white);font-weight:700;font-size:15px;display:flex;align-items:center;justify-content:center;padding-right:20px}
.card .cart em{width:50px;background:var(--black);display:flex;align-items:center;justify-content:center}
.card .stars{position:absolute;top:348px;width:100%;color:var(--green-lime);font-size:12px;letter-spacing:2px}
.card .rev{position:absolute;top:370px;width:100%;font-size:12px;color:var(--muted)}

/* about */
.about-copy{left:675px;top:1770px;width:420px;font-size:14px;line-height:31px;color:var(--muted)}
.about-copy p+p{margin-top:31px}

/* features */
.band{left:0;top:2247px;width:1200px;height:133px;background:var(--green-band)}
.feat{position:absolute;top:2284px;display:flex;gap:22px;color:var(--white)}
.feat h4{font-family:'Montserrat',sans-serif;font-weight:700;font-size:17px;margin-top:2px}
.feat p{font-size:13px;margin-top:10px}

/* faq */
.faq-open{left:153px;top:2590px;width:894px;height:290px;background:var(--panel);border-left:4px solid var(--green-lime)}
.faq-q{position:absolute;left:200px;font-family:'Montserrat',sans-serif;font-weight:700;font-size:15px;color:var(--ink);white-space:nowrap}
.faq-arrow{position:absolute;left:174px;width:0;height:0}
.faq-a{left:200px;width:800px;font-size:12.5px;line-height:26px;color:var(--muted)}
.faq-a p+p{margin-top:25px}
.sep{position:absolute;left:153px;width:894px;height:1px;background:var(--line)}

/* newsletter */
.news{left:0;top:3233px;width:1200px;height:385px;background:linear-gradient(90deg,#7a9a1e 0%,#6f9424 50%,#88a620 100%)}
.news-div{left:599px;top:3293px;width:2px;height:262px;background:rgba(255,255,255,.8)}
.center-w{text-align:center;color:var(--white)}

/* footer */
.foot{left:0;top:3618px;width:1200px;height:376px;background:var(--black)}
.foot-brand{left:0;width:1200px;top:3752px;text-align:center;font-weight:900;font-size:40px;color:var(--white)}
.foot-nav a{position:absolute;top:3846px;color:var(--white);font-size:15px;text-decoration:none;white-space:nowrap}
.pay{position:absolute;top:3900px;width:40px;height:26px;border-radius:5px;background:var(--white)}
.copy{left:0;width:1200px;top:3951px;text-align:center;color:var(--white);font-size:13px}
</style>
</head>
<body>

<div class="abs topbar"><span>100% Legal across the US</span></div>

<div class="abs brand"><i></i>Sunleaf Hemp</div>

<div class="abs search">Search Products
  <svg width="16" height="16" viewBox="0 0 16 16"><circle cx="6.5" cy="6.5" r="5" fill="none" stroke="#86a21d" stroke-width="2"/><line x1="10" y1="10" x2="14.5" y2="14.5" stroke="#86a21d" stroke-width="2"/></svg>
</div>
<div class="abs util" style="left:862px">
  <svg width="18" height="18" viewBox="0 0 18 18"><circle cx="9" cy="9" r="8" fill="none" stroke="#86a21d" stroke-width="1.5"/><line x1="9" y1="8" x2="9" y2="13" stroke="#86a21d" stroke-width="1.5"/><circle cx="9" cy="5.3" r="1" fill="#86a21d"/></svg>Contact Us</div>
<div class="abs" style="left:1000px;top:74px;width:1px;height:18px;background:#999"></div>
<div class="abs util" style="left:1034px">
  <svg width="16" height="18" viewBox="0 0 16 18"><rect x="1.5" y="6" width="13" height="11" fill="none" stroke="#86a21d" stroke-width="1.5"/><path d="M5 6V4a3 3 0 0 1 6 0v2" fill="none" stroke="#86a21d" stroke-width="1.5"/></svg>Cart</div>
<nav class="abs nav">
  <a style="left:432px">Home</a><a style="left:541px">About Us</a><a style="left:672px">Why Choose Us?</a><a style="left:854px">Our Products</a><a style="left:1014px">Contact Us</a>
</nav>

<div class="abs hero" role="img" aria-label="Dropper releasing hemp oil into a glass bottle beside a wooden spoon of seeds and green hemp leaves"></div>
<h1 class="abs hero-title">CANNABIS<br>PRODUCTS ARE<br>100% LEGAL ACROSS<br>THE US</h1>
<a class="btn btn-lime" style="left:110px;top:585px;width:127px;height:43px">Get Started</a>

<div class="mark" style="left:580px;top:858px"></div>
<h2 class="h2" style="left:0;width:1200px;text-align:center;top:883px">SHOP OUR PRODUCTS</h2>

<div class="card" style="left:85px">
  <div class="photo" role="img" aria-label="Amber dropper bottle with hemp buds and vape pen" style="background:linear-gradient(#f7f4ef,#e6ddcf)"></div>
  <h3>Concentrates</h3><div class="price">Min <b>$ 45.00</b> / Bottle</div>
  <div class="cart"><span>Add To Cart</span><em><svg width="14" height="12" viewBox="0 0 14 12"><path d="M0 1h3l2 7h7l2-5H4" fill="none" stroke="#fff" stroke-width="1.6"/><circle cx="6" cy="10.5" r="1.2" fill="#fff"/><circle cx="11" cy="10.5" r="1.2" fill="#fff"/></svg></em></div>
  <div class="stars">★★★★☆</div><div class="rev">(1234+ Reviews)</div>
</div>
<div class="card active" style="left:351px">
  <div class="photo" role="img" aria-label="Amber bottles, capsules and stethoscope" style="background:linear-gradient(#f6f3ee,#e2d5c6)"></div>
  <h3>Concentrates</h3><div class="price">Min <b>$ 45.00</b> / Bottle</div>
  <div class="cart"><span>Add To Cart</span><em><svg width="14" height="12" viewBox="0 0 14 12"><path d="M0 1h3l2 7h7l2-5H4" fill="none" stroke="#fff" stroke-width="1.6"/><circle cx="6" cy="10.5" r="1.2" fill="#fff"/><circle cx="11" cy="10.5" r="1.2" fill="#fff"/></svg></em></div>
  <div class="stars">★★★★☆</div><div class="rev">(1234+ Reviews)</div>
</div>
<div class="card" style="left:615px">
  <div class="photo" role="img" aria-label="Dried hemp flower bud" style="background:linear-gradient(#f6f6f2,#d9d3b8)"></div>
  <h3>Concentrates</h3><div class="price">Min <b>$ 45.00</b> / Bottle</div>
  <div class="cart"><span>Add To Cart</span><em><svg width="14" height="12" viewBox="0 0 14 12"><path d="M0 1h3l2 7h7l2-5H4" fill="none" stroke="#fff" stroke-width="1.6"/><circle cx="6" cy="10.5" r="1.2" fill="#fff"/><circle cx="11" cy="10.5" r="1.2" fill="#fff"/></svg></em></div>
  <div class="stars">★★★★☆</div><div class="rev">(1234+ Reviews)</div>
</div>
<div class="card" style="left:879px">
  <div class="photo" role="img" aria-label="Tincture bottles, gummies and hemp buds in a bowl" style="background:linear-gradient(#f7f4ee,#e0d2bd)"></div>
  <h3>Concentrates</h3><div class="price">Min <b>$ 45.00</b> / Bottle</div>
  <div class="cart"><span>Add To Cart</span><em><svg width="14" height="12" viewBox="0 0 14 12"><path d="M0 1h3l2 7h7l2-5H4" fill="none" stroke="#fff" stroke-width="1.6"/><circle cx="6" cy="10.5" r="1.2" fill="#fff"/><circle cx="11" cy="10.5" r="1.2" fill="#fff"/></svg></em></div>
  <div class="stars">★★★★☆</div><div class="rev">(1234+ Reviews)</div>
</div>

<a class="btn btn-dark" style="left:445px;top:1460px;width:155px;height:42px">View Products</a>
<a class="btn btn-lime" style="left:628px;top:1460px;width:127px;height:42px">Get Started</a>

<div class="abs" role="img" aria-label="Close-up of a green hemp flower" style="left:112px;top:1641px;width:436px;height:487px;background:linear-gradient(135deg,#c9d86a,#6f9a2e 55%,#3f6a22)"></div>
<div class="abs" role="img" aria-label="Two tincture bottles on a wooden surface" style="left:381px;top:1750px;width:244px;height:328px;background:linear-gradient(160deg,#5f8a3a,#2f4a22 70%,#8b6a48)"></div>

<div class="mark" style="left:677px;top:1676px"></div>
<h2 class="h2" style="left:677px;top:1705px">ABOUT US</h2>
<div class="abs about-copy">
  <p>Sed ut perspiciatis unde omnis iste natus error sit voluptatem accusantium doloremque laudantium, totam rem aperiam, eaque ipsa quae ab illo inventore veritatis et quasi architecto beatae vitae dicta sunt explicabo.</p>
  <p>Nemo enim ipsam voluptatem quia voluptas sit aspernatur aut odit aut fugit, sed quia consequuntur magni dolores eos qui ratione voluptatem sequi nesciunt. Neque porro quisquam est, qui dolorem ipsum quia dolor sit amet</p>
</div>
<a class="btn btn-lime" style="left:675px;top:2072px;width:126px;height:42px">Read More</a>

<div class="abs band"></div>
<div class="feat" style="left:110px">
  <svg width="66" height="58" viewBox="0 0 66 58"><path d="M2 14h30M2 14v40h44V34" fill="none" stroke="#fff" stroke-width="2.5"/><line x1="8" y1="30" x2="24" y2="30" stroke="#fff" stroke-width="2.5"/><line x1="8" y1="40" x2="24" y2="40" stroke="#fff" stroke-width="2.5"/><path d="M48 2l14 5v12c0 10-7 16-14 19-7-3-14-9-14-19V7z" fill="none" stroke="#fff" stroke-width="2.5"/><path d="M41 19l5 5 9-9" fill="none" stroke="#fff" stroke-width="2.5"/></svg>
  <div><h4>Fast &amp; Secure</h4><p>Sed ut perspiciatis unde omnis</p></div>
</div>
<div class="feat" style="left:460px">
  <svg width="66" height="66" viewBox="0 0 66 66"><circle cx="33" cy="33" r="26" fill="none" stroke="#fff" stroke-width="2.5"/><line x1="33" y1="20" x2="33" y2="60" stroke="#fff" stroke-width="2.5"/></svg>
  <div><h4>100% Hemp Derived</h4><p>Sed ut perspiciatis unde omnis</p></div>
</div>
<div class="feat" style="left:800px">
  <svg width="74" height="50" viewBox="0 0 74 50"><rect x="2" y="4" width="44" height="32" fill="none" stroke="#fff" stroke-width="2.5"/><path d="M46 14h14l10 12v10H46" fill="none" stroke="#fff" stroke-width="2.5"/><circle cx="16" cy="42" r="5" fill="var(--green-band)" stroke="#fff" stroke-width="2.5"/><circle cx="58" cy="42" r="5" fill="var(--green-band)" stroke="#fff" stroke-width="2.5"/><path d="M16 20l6 6 11-11" fill="none" stroke="#fff" stroke-width="2.5"/></svg>
  <div><h4>Free Shipping</h4><p>Sed ut perspiciatis unde omnis</p></div>
</div>

<div class="mark" style="left:580px;top:2468px"></div>
<h2 class="h2" style="left:0;width:1200px;text-align:center;top:2494px">FREQENTLY ASKED QUESTIONS</h2>

<div class="abs faq-open"></div>
<svg class="abs" style="left:172px;top:2626px" width="12" height="8" viewBox="0 0 12 8"><path d="M1 1h10L6 7z" fill="#86a21d"/></svg>
<div class="faq-q" style="top:2620px">Sed ut perspiciatis unde omnis iste natus error?</div>
<div class="abs faq-a" style="top:2652px">
  <p>I must explain to you how all this mistaken idea of denouncing pleasure and praising pain was born and I will give you a complete account of the system, and expound the actual teachings of the great explorer of the truth, the master-builder of human happiness. No one rejects, dislikes, or avoids pleasure itself, because it is pleasure, but because those who do not know how to pursue pleasure rationally encounter consequences that are extremely painful.</p>
  <p>Nor again is there anyone who loves or pursues or desires to obtain pain of itself, because it is pain, but because occasionally circumstances occur in which toil and pain can procure him some great pleasure. To take a trivial example, which of us ever undertakes laborious physical exercise, except to obtain some advantage from it?</p>
</div>

<svg class="abs" style="left:175px;top:2922px" width="7" height="12" viewBox="0 0 7 12"><path d="M1 1l5 5-5 5z" fill="#111"/></svg>
<div class="faq-q" style="top:2917px">Sed ut perspiciatis unde omnis iste natus error?</div>
<div class="sep" style="top:2954px"></div>
<svg class="abs" style="left:175px;top:2983px" width="7" height="12" viewBox="0 0 7 12"><path d="M1 1l5 5-5 5z" fill="#111"/></svg>
<div class="faq-q" style="top:2978px">Quasi architecto beatae vitae dicta sunt explicabo. Nemo enim ipsam voluptatem?</div>
<div class="sep" style="top:3015px"></div>
<svg class="abs" style="left:175px;top:3043px" width="7" height="12" viewBox="0 0 7 12"><path d="M1 1l5 5-5 5z" fill="#111"/></svg>
<div class="faq-q" style="top:3038px">Vel illum qui dolorem eum fugiat quo voluptas nulla pariatur?</div>
<div class="sep" style="top:3076px"></div>
<svg class="abs" style="left:175px;top:3104px" width="7" height="12" viewBox="0 0 7 12"><path d="M1 1l5 5-5 5z" fill="#111"/></svg>
<div class="faq-q" style="top:3099px">Annoying consequences, or one who avoids a pain that produces no resultant pleasure?</div>
<div class="sep" style="top:3137px"></div>

<div class="abs news"></div>
<div class="abs news-div"></div>
<div class="abs center-w" style="left:152px;width:364px;top:3325px">
  <div class="head-font" style="font-weight:700;font-size:29px">Join Our Newsletter</div>
  <div style="font-size:13.5px;line-height:25px;margin-top:22px">On the other hand, we denounce with<br>righteous indignation and dislike men who are so<br>beguiled and demoralized</div>
</div>
<div class="abs" style="left:152px;top:3478px;width:230px;height:42px;background:#fff;font-size:14px;color:var(--muted);padding:13px 26px">Email Address</div>
<div class="abs" style="left:382px;top:3478px;width:134px;height:42px;background:#000;color:#fff;font-weight:700;font-size:14px;display:flex;align-items:center;justify-content:center">Subscribe Now</div>

<div class="abs center-w" style="left:700px;width:315px;top:3330px">
  <div style="font-size:18px;letter-spacing:3px">★★★★☆</div>
  <div style="font-size:13.5px;margin-top:16px">Ratings and reviews (4.1/5) Store</div>
  <div style="font-weight:900;font-size:19px;margin-top:6px">Sunleaf Hemp</div>
  <div style="font-size:13.5px;margin-top:8px">Bsed on 425 ratings and 371 user review</div>
</div>
<div class="abs" style="left:790px;top:3474px;width:135px;height:44px;border:2px solid #fff;color:#fff;font-weight:700;font-size:14px;display:flex;align-items:center;justify-content:center">Write A Review</div>

<div class="abs foot"></div>
<div class="abs foot-brand">Sunleaf Hemp</div>
<div class="foot-nav">
  <a style="left:271px">Home</a><a style="left:380px">About Us</a><a style="left:511px">Why Choose Us?</a><a style="left:693px">Our Products</a><a style="left:853px">Contact Us</a>
</div>
<div class="pay" style="left:450px"></div>
<div class="pay" style="left:500px"></div>
<div class="pay" style="left:550px"></div>
<div class="pay" style="left:603px"></div>
<div class="pay" style="left:654px"></div>
<div class="pay" style="left:705px"></div>
<div class="abs copy">(C) Copyright 2023 | All Rights Reserved.</div>

</body>
</html>
```